Vindgerdi - Start-up company selling electricity

Hello let me tell you about Vindgerdi.

Vindgerdi is start-up company selling electricity in Iceland. The operations of the company consist of making power usage forecasts for our customers, purchasing the electricity wholesale from the energy producers, and selling the electricity to the consumer. We are focused on tech by using optimization and machine learning to minimize electricity prices to our customers. Our marketing strategy is to portray a tech company mindset and to show dedication to driving down the electricity price on the market.

We need your help to make our website pop. Possible concepts to work with are as follows:

- Iceland the land of ice and fire
- Green energy
- Innovation
- Tech and data science

Link to our website: https://prufa.vindgerdi-example.is/
We are open to ideas.
Thank you!

Target Market(s)

Electricity consumers both homes and companies.

Number of Pages Required

1 page

Font styles to use
Serif
Sans Serif

```html
<!DOCTYPE html>
<html lang="en">
<head>
<meta charset="utf-8">
<title>Vindgerdi – Same electricity, just cheaper</title>
<link href="https://fonts.googleapis.com/css2?family=IBM+Plex+Serif:wght@400;600;700&family=Nunito+Sans:wght@400;600&family=Roboto:wght@500;700&display=swap" rel="stylesheet">
<style>
:root{
  --red:#8f2323;
  --red-deep:#7a1c1c;
  --navy:#13264d;
  --navy-deep:#0e1d3d;
  --ink:#222;
  --muted:#444;
  --white:#fff;
  --rule:#d8d8d8;
  --serif:'IBM Plex Serif',Georgia,serif;
  --sans:'Nunito Sans',Arial,sans-serif;
  --ui:'Roboto',Arial,sans-serif;
}
*{margin:0;padding:0;box-sizing:border-box}
html,body{width:1200px;height:2373px;overflow:hidden;background:var(--white)}
body{position:relative;font-family:var(--sans);color:var(--ink)}
.abs{position:absolute}

/* top bar */
.topbar{left:0;top:0;width:1200px;height:40px;background:var(--red);color:var(--white);font-family:var(--ui);font-weight:700;font-size:17px}
.topbar .contact{position:absolute;top:7px;display:flex;align-items:center;gap:12px}
.topbar .dot{width:27px;height:27px;border-radius:50%;background:var(--navy);display:flex;align-items:center;justify-content:center}
.social{position:absolute;right:144px;top:7px;display:flex;gap:10px}
.social span{width:26px;height:26px;border:1.5px solid var(--white);border-radius:50%}

/* hero */
.hero{left:0;top:40px;width:1200px;height:790px}
.brand{left:144px;top:92px;font-family:var(--serif);font-size:40px;color:var(--white);letter-spacing:1px;display:flex;align-items:center;gap:14px}
.brand i{width:34px;height:34px;border-radius:50%;background:var(--white);display:block}
.nav{top:107px;right:145px;display:flex;gap:27px;font-family:var(--serif);font-weight:700;font-size:15px;color:var(--white);text-transform:uppercase}
.hero-title{left:144px;top:333px;font-family:var(--serif);font-weight:700;font-size:40px;line-height:48px;color:var(--white);text-transform:uppercase}
.btn{display:flex;align-items:center;justify-content:center;border-radius:30px;font-family:var(--serif);font-weight:700;font-size:16px;text-transform:uppercase;color:var(--white)}
.btn-red{background:var(--red)}
.btn-navy{background:var(--navy)}
.btn-line{border:2px solid var(--white)}
.hero-btn{left:144px;top:449px;width:199px;height:49px}
.dots{left:562px;top:737px;display:flex;gap:9px;align-items:center}
.dots span{width:11px;height:11px;border-radius:50%;background:var(--white)}
.dots span.on{width:20px;height:20px;border:2px solid var(--white);background:radial-gradient(var(--white) 45%,transparent 50%)}

/* welcome */
.welcome-art{left:144px;top:880px;width:323px;height:439px}
.divider{left:533px;top:926px;width:1px;height:371px;background:var(--rule)}
.welcome-title{left:605px;top:918px;font-family:var(--serif);font-weight:700;font-size:42px;color:var(--ink)}
.welcome-text{left:605px;top:991px;width:455px;font-size:14.5px;line-height:20.8px;color:var(--muted)}
.btn-company{left:605px;top:1214px;width:173px;height:45px}
.btn-home{left:798px;top:1214px;width:173px;height:45px}

/* split */
.split{left:0;top:1360px;width:1200px;height:680px}
.panel{text-align:center;color:var(--white)}
.panel-left{left:0;width:623px;top:1478px}
.panel-right{left:593px;width:584px;top:1490px}
.panel h2{font-family:var(--serif);font-weight:600;font-size:31px;line-height:35px}
.price{font-family:var(--serif);font-size:20px;margin-top:4px}
.price b{font-size:40px;font-weight:700;margin-right:8px}
.panel .note{font-family:var(--serif);font-size:20px;line-height:28px;margin-top:12px}
.panel .copy{font-size:15.5px;line-height:22.5px;font-weight:600;width:360px;margin:14px auto 0}
.panel .btn{margin:26px auto 0;width:157px;height:44px;font-size:15px}

/* footer */
.foot-brand{left:0;top:2020px;width:1200px;display:flex;justify-content:center;align-items:center;gap:16px;font-family:var(--serif);font-weight:600;font-size:53px;color:var(--red)}
.foot-brand i{width:46px;height:46px;border-radius:50%;background:var(--navy);display:block}
.info{top:2131px;display:flex;align-items:center;gap:19px}
.info .ring{width:59px;height:59px;border:2px solid var(--navy);border-radius:50%;display:flex;align-items:center;justify-content:center}
.info h4{font-family:var(--ui);font-weight:500;font-size:16px;color:var(--ink)}
.info p{font-size:16px;color:var(--muted);margin-top:3px}
.foot-rule{left:146px;top:2225px;width:908px;height:1px;background:var(--rule)}
.legal{left:0;width:1200px;text-align:center;font-size:16px;color:var(--muted)}
</style>
</head>
<body>

<header class="abs topbar">
  <div class="contact" style="left:144px">
    <span class="dot"><svg width="13" height="13" viewBox="0 0 24 24"><path fill="#fff" d="M6.6 10.8a15 15 0 006.6 6.6l2.2-2.2a1 1 0 011-.25 11.4 11.4 0 003.6.57 1 1 0 011 1V20a1 1 0 01-1 1A17 17 0 013 4a1 1 0 011-1h3.5a1 1 0 011 1 11.4 11.4 0 00.57 3.6 1 1 0 01-.25 1z"/></svg></span>
    Call 410-7788
  </div>
  <div class="contact" style="left:344px">
    <span class="dot"><svg width="13" height="11" viewBox="0 0 24 18"><path fill="#fff" d="M0 2l12 8 12-8V0H0zm0 3v13h24V5l-12 8z"/></svg></span>
    vindgerdi@vindgerdi-example.is
  </div>
  <div class="social"><span></span><span></span><span></span><span></span><span></span></div>
</header>

<section class="abs hero">
  <svg width="1200" height="790" viewBox="0 0 1200 790" role="img" aria-label="Photo of two engineers walking through a server room with a glowing blue data network">
    <defs>
      <linearGradient id="heroFill" x1="0" y1="0" x2="1" y2="0">
        <stop offset="0" stop-color="#0b1526"/>
        <stop offset=".45" stop-color="#26344a"/>
        <stop offset=".75" stop-color="#0f3a66"/>
        <stop offset="1" stop-color="#0a2446"/>
      </linearGradient>
    </defs>
    <polygon points="0,0 1200,0 1200,710 604,790 0,700" fill="var(--red)"/>
    <polygon points="0,0 1200,0 1200,700 604,780 0,693" fill="url(#heroFill)"/>
  </svg>
</section>

<div class="abs brand"><i></i>VINDGERDI</div>
<nav class="abs nav"><span>Terms of business</span><span>Question &amp; answer</span><span>About Vindgerdi</span></nav>
<h1 class="abs hero-title">Same electricity<br>~ just cheaper!</h1>
<a class="abs btn btn-red hero-btn">Learn more</a>
<div class="abs dots"><span class="on"></span><span></span><span></span><span></span></div>

<svg class="abs welcome-art" viewBox="0 0 323 439" role="img" aria-label="Illustration of a hand touching a glowing light bulb above a city at night">
  <defs>
    <linearGradient id="artFill" x1="0" y1="0" x2="0" y2="1">
      <stop offset="0" stop-color="#e7866a"/>
      <stop offset=".45" stop-color="#5a3f6e"/>
      <stop offset="1" stop-color="#1f3f86"/>
    </linearGradient>
  </defs>
  <circle cx="161" cy="270" r="161" fill="url(#artFill)"/>
</svg>
<div class="abs divider"></div>
<h2 class="abs welcome-title">Welcome to business</h2>
<p class="abs welcome-text">Sed ut perspiciatis unde omnis iste natus error sit voluptatem accusantium doloremque laudantium, totam rem aperiam, eaque ipsa quae ab illo inventore veritatis et quasi architecto beatae vitae dicta sunt explicabo. Nemo enim ipsam voluptatem quia voluptas sit aspernatur aut odit aut fugit, sed quia consequuntur magni dolores eos qui ratione voluptatem sequi nesciunt. Neque porro quisquam est, qui dolorem ipsum quia dolor sit amet, consectetur, adipisci velit, sed quia non numquam eius modi tempora incidunt ut labore et dolore magnam aliquam quaerat voluptatem.</p>
<a class="abs btn btn-red btn-company">Company</a>
<a class="abs btn btn-navy btn-home">Home</a>

<svg class="abs split" viewBox="0 0 1200 680">
  <defs>
    <linearGradient id="leftFill" x1="0" y1="0" x2="0" y2="1">
      <stop offset="0" stop-color="#922828"/>
      <stop offset="1" stop-color="#a4301f"/>
    </linearGradient>
    <linearGradient id="rightFill" x1="0" y1="0" x2="0" y2="1">
      <stop offset="0" stop-color="#15284f"/>
      <stop offset=".7" stop-color="#1b2b55"/>
      <stop offset="1" stop-color="#202a4c"/>
    </linearGradient>
  </defs>
  <polygon points="0,8 1200,8 1200,48 0,48" fill="var(--navy)"/>
  <polygon points="0,8 593,50 593,400 0,400" fill="var(--navy)"/>
  <g role="img" aria-label="Photo of wind turbines over a field at dusk, tinted red">
    <polygon points="0,45 593,54 593,586 0,630" fill="url(#leftFill)"/>
  </g>
  <polygon points="593,586 1200,666 1200,646 593,566" fill="var(--red)"/>
  <g role="img" aria-label="Photo of a city skyline at night with rising data lines, tinted navy">
    <polygon points="593,54 1200,8 1200,646 593,566" fill="url(#rightFill)"/>
  </g>
</svg>

<div class="abs panel panel-left">
  <svg width="92" height="105" viewBox="0 0 92 105" fill="none" stroke="#fff" stroke-width="4" stroke-linecap="round">
    <line x1="46" y1="2" x2="46" y2="12"/><line x1="33" y1="6" x2="33" y2="14"/><line x1="59" y1="6" x2="59" y2="14"/>
    <circle cx="46" cy="45" r="22"/>
    <path d="M53 36c-2-3-12-4-13 1s13 4 13 10-12 6-14 2M46 30v30"/>
    <rect x="4" y="72" width="12" height="30"/>
    <path d="M16 78h20c6 0 10 6 16 6h10M16 98h26c12 0 30-10 44-20-4-6-12-4-20 2"/>
  </svg>
  <h2 style="margin-top:22px">Price list</h2>
  <div class="price"><b>6.95</b>ISK / kWh</div>
  <div class="price"><b>6.22</b>ISK / kWh</div>
  <p class="note">electric acceleration<br>Make a price comparison</p>
  <a class="btn btn-line" style="margin-top:26px">Verðvaki</a>
</div>

<div class="abs panel panel-right">
  <svg width="96" height="96" viewBox="0 0 96 96" fill="none" stroke="#fff" stroke-width="4" stroke-linejoin="round" stroke-linecap="round">
    <path d="M18 22A42 42 0 0188 40M78 74A42 42 0 018 56"/>
    <path d="M82 28l6 12 10-8M14 68l-6-12-10 8"/>
    <path d="M54 18L32 52h16l-6 28 24-38H50z"/>
  </svg>
  <h2 style="margin-top:36px">PricThe future is<br>excitinge list</h2>
  <p class="copy">Let's make the electricity system smarter together. Vindgerdi uses artificial intelligence, data science and automation to minimize costs and promote eccentricity</p>
  <a class="btn btn-line" style="margin-top:30px">Learn more</a>
</div>

<div class="abs foot-brand"><i></i>VINDGERDI</div>

<div class="abs info" style="left:170px">
  <span class="ring"><svg width="20" height="26" viewBox="0 0 20 26"><path fill="var(--red)" d="M10 0a10 10 0 0110 10c0 7-10 16-10 16S0 17 0 10A10 10 0 0110 0zm0 6a4 4 0 100 8 4 4 0 000-8z"/></svg></span>
  <div><h4>ADDRESS</h4><p style="font-size:15px">Lækjarbraut 4 170 Dalsnes</p></div>
</div>
<div class="abs info" style="left:533px">
  <span class="ring"><svg width="24" height="24" viewBox="0 0 24 24"><path fill="var(--red)" d="M6.6 10.8a15 15 0 006.6 6.6l2.2-2.2a1 1 0 011-.25 11.4 11.4 0 003.6.57 1 1 0 011 1V20a1 1 0 01-1 1A17 17 0 013 4a1 1 0 011-1h3.5a1 1 0 011 1 11.4 11.4 0 00.57 3.6 1 1 0 01-.25 1z"/></svg></span>
  <div><h4>PHONE</h4><p>410-7788</p></div>
</div>
<div class="abs info" style="left:768px">
  <span class="ring"><svg width="26" height="20" viewBox="0 0 24 18"><path fill="var(--red)" d="M0 2l12 8 12-8V0H0zm0 3v13h24V5l-12 8z"/></svg></span>
  <div><h4>EMAIL</h4><p>vindgerdi@vindgerdi-example.is</p></div>
</div>

<div class="abs foot-rule"></div>
<p class="abs legal" style="top:2256px">Vindgerdi ehf ID number: 510101-0420 | VAT number: 100234</p>
<p class="abs legal" style="top:2295px">VINDGERDI © 2021 All Rights Reserved | Privacy policy</p>

</body>
</html>
```